New Business Card

Need new business cards like attached. if possible add QR code. Vertical Business Card

I need creative and unique business card design using my company logo. Ok to change logo color. We are a small brokerage doing both Real Estate and Mortgage services. Need to have the follow on business card;
1. agent name - Nola Brenner - Realtor
2. cell - 949-555-2146
3. license number - DRE 07461392
4. business name - Tallow Ridge Realty & Lending, Inc
5. business office - 626-555-4817
6. business address - 482 W. Larkmoor Ave #212, Arcadia CA 91006
7. business logo - attached (ok to use different color on logo)

```html
<!DOCTYPE html>
<html lang="en">
<head>
<meta charset="utf-8">
<title>Tallow Ridge Realty &amp; Lending — Business Card</title>
<link rel="stylesheet" href="https://fonts.googleapis.com/css2?family=Montserrat:wght@500;600&family=Roboto:ital,wght@0,400;1,400;1,900&display=swap">
<style>
  :root {
    --stage: #222223;
    --card-white: #ffffff;
    --card-dark: #18191b;
    --card-dark-edge: #2a2b2e;
    --grid-line: #0c0d0e;
    --brand-blue: #1f4fa8;
    --accent-blue: #0a8fd8;
    --ink: #141414;
  }
  * { box-sizing: border-box; margin: 0; padding: 0; }
  html, body { width: 1200px; height: 780px; overflow: hidden; }
  body {
    background: var(--stage);
    font-family: "Roboto", Arial, sans-serif;
    display: flex;
    align-items: center;
    justify-content: center;
    gap: 70px;
  }
  .card {
    width: 340px;
    height: 595px;
    border-radius: 26px;
    overflow: hidden;
    box-shadow: 0 18px 40px rgba(0, 0, 0, 0.45);
  }
  .card-back {
    position: relative;
    background: var(--card-dark);
  }
  .card-back .pattern { width: 100%; height: 100%; display: block; }
  .card-back .corner-mark {
    position: absolute;
    left: 236px;
    top: 438px;
    width: 46px;
    height: 46px;
    background: linear-gradient(160deg, var(--accent-blue), var(--brand-blue));
  }
  .card-front {
    background: var(--card-white);
    display: flex;
    flex-direction: column;
    align-items: center;
    text-align: center;
    padding: 54px 22px 0;
  }
  .brand {
    display: flex;
    flex-direction: column;
    align-items: center;
    gap: 22px;
    color: var(--brand-blue);
  }
  .brand-square {
    width: 104px;
    height: 104px;
    background: var(--brand-blue);
  }
  .brand-name {
    font-family: "Montserrat", Arial, sans-serif;
    font-weight: 600;
    font-size: 16px;
    letter-spacing: 0.22em;
    line-height: 1.55;
    text-transform: uppercase;
  }
  .agent { margin-top: 52px; }
  .agent-name {
    font-weight: 900;
    font-style: italic;
    font-size: 24px;
    color: var(--brand-blue);
    text-transform: uppercase;
    letter-spacing: 0.01em;
  }
  .agent-title { font-size: 18px; color: var(--ink); margin-top: 2px; }
  .rule {
    width: 54px;
    height: 2px;
    background: var(--brand-blue);
    margin: 12px auto;
  }
  .phones { font-size: 18px; line-height: 1.3; color: var(--ink); font-style: italic; }
  .office-name { font-size: 16px; color: var(--brand-blue); font-style: italic; }
  .office-address { font-size: 16px; line-height: 1.3; color: var(--ink); margin-top: 3px; }
  .license { font-size: 18px; color: var(--ink); }
  .license .label { color: var(--brand-blue); }
</style>
</head>
<body>
  <section class="card card-back" aria-label="Card back">
    <svg class="pattern" viewBox="0 0 340 595" role="img" aria-label="Embossed repeating brand-mark pattern in dark charcoal tones">
      <defs>
        <linearGradient id="backShade" x1="0" y1="0" x2="1" y2="1">
          <stop offset="0" stop-color="#2e2f32"/>
          <stop offset="1" stop-color="#111213"/>
        </linearGradient>
      </defs>
      <rect width="340" height="595" fill="url(#backShade)"/>
    </svg>
    <div class="corner-mark" role="img" aria-label="Tallow Ridge brand mark placeholder"></div>
  </section>

  <section class="card card-front" aria-label="Card front">
    <header class="brand">
      <div class="brand-square" aria-hidden="true"></div>
      <p class="brand-name">Tallow Ridge<br>Realty &amp; Lending, Inc</p>
    </header>

    <div class="agent">
      <h1 class="agent-name">Nola Brenner</h1>
      <p class="agent-title">Realtor</p>
    </div>

    <div class="rule"></div>

    <p class="phones">949-555-2146<br>626-555-4817</p>

    <div class="rule"></div>

    <p class="office-name">Tallow Ridge Realty &amp; Lending, Inc</p>
    <p class="office-address">482 W. Larkmoor Ave #212,<br>Arcadia CA 91006</p>

    <div class="rule"></div>

    <p class="license"><span class="label">LIC</span> DRE 07461392</p>
  </section>
</body>
</html>
```